Animal Eye Clinic needs a Business card

We are a new veterinary ophthalmology practice (Ridgeline Pet Vision Care) and we need a business card designed. We only see animal eyes - we are not a regular veterinary clinic. We already have a logo. We are looking for a professional, good looking business card to hand out to our clients. We are looking for something simple but professional and contemporary. Our logo is likely the only picture/graphic that needs to be on the card.
Updates

Contact Information for Business Card

Delia Vossman, BSc, DVM, MSc, DipACVO
Veterinary Ophthalmologist

Phone: 250.418.3927
Email: ridgelinepetvisioncare@mailbox-example.net
Website: ridgelinepetvisioncare-example.net
Address: 1874 Thornbury Rd
Kelowna, BC, V1X 4M9

Colors

Designer to choose colors to be used in the design.

Requirements
Must have
• Our logo (attached)

```html
<!DOCTYPE html>
<html lang="en">
<head>
<meta charset="utf-8">
<title>Ridgeline Pet Vision Care – Business Card</title>
<link href="https://fonts.googleapis.com/css2?family=Exo+2:ital,wght@0,700;1,700&family=Montserrat:ital,wght@0,400;0,700;1,400&display=swap" rel="stylesheet">
<style>
  :root {
    --stage: #5e5e5e;
    --card: #2d2e30;
    --card-deep: #232426;
    --art-light: #3d3e41;
    --art-dark: #1c1d1f;
    --teal: #0f8d9c;
    --white: #f2f2f2;
  }
  * { box-sizing: border-box; margin: 0; padding: 0; }
  html, body { width: 1200px; height: 1125px; overflow: hidden; }
  body {
    background: var(--stage);
    font-family: "Montserrat", sans-serif;
    display: flex;
    flex-direction: column;
    align-items: center;
    justify-content: center;
    gap: 56px;
  }
  .card {
    position: relative;
    width: 840px;
    height: 480px;
    background: var(--card);
    border-bottom: 6px solid var(--teal);
    box-shadow: 0 10px 24px rgba(0,0,0,.35);
    overflow: hidden;
  }
  .card-art {
    position: absolute;
    border-radius: 48% 52% 40% 60% / 50% 45% 55% 50%;
    background: radial-gradient(ellipse at 40% 40%, var(--art-light), var(--art-dark) 80%);
  }
  /* back */
  .card--back .card-art { left: 60px; top: 50px; width: 440px; height: 400px; }
  .back-name {
    position: absolute;
    right: 48px;
    top: 200px;
    font-family: "Exo 2", sans-serif;
    font-weight: 700;
    font-size: 34px;
    text-transform: uppercase;
    color: var(--teal);
    text-align: right;
  }
  /* front */
  .card--front .card-art { right: 30px; top: 30px; width: 400px; height: 430px; }
  .brand {
    position: absolute;
    left: 46px;
    top: 40px;
    display: flex;
    align-items: center;
    gap: 14px;
  }
  .brand-dot { width: 40px; height: 40px; border-radius: 50%; background: var(--teal); }
  .brand-name {
    font-family: "Exo 2", sans-serif;
    font-weight: 700;
    font-size: 26px;
    text-transform: uppercase;
    color: var(--teal);
  }
  .contact-block { position: absolute; left: 46px; top: 120px; z-index: 1; }
  .person-name {
    display: flex;
    align-items: center;
    gap: 12px;
    font-family: "Exo 2", sans-serif;
    font-style: italic;
    font-weight: 700;
    font-size: 30px;
    text-transform: uppercase;
    color: var(--teal);
  }
  .person-name svg { width: 20px; height: 22px; fill: var(--teal); }
  .credentials { margin-left: 32px; font-size: 19px; font-style: italic; color: var(--teal); }
  .role { margin-left: 32px; font-size: 20px; color: var(--white); margin-top: 2px; }
  .address { margin-top: 26px; font-size: 20px; line-height: 1.3; color: var(--white); }
  .contact-list { list-style: none; margin-top: 14px; }
  .contact-list li {
    display: flex; align-items: center; gap: 8px;
    font-size: 20px; line-height: 1.45; color: var(--white);
  }
  .contact-list svg { width: 18px; height: 18px; flex: none; }
</style>
</head>
<body>

<section class="card card--back" aria-label="Business card back">
  <div class="card-art" role="img" aria-label="Embossed illustration of a horse, dog and cat heads"></div>
  <p class="back-name">Ridgeline Pet Vision Care</p>
</section>

<section class="card card--front" aria-label="Business card front">
  <div class="card-art" role="img" aria-label="Embossed illustration of a horse, dog and cat heads"></div>

  <div class="brand">
    <span class="brand-dot"></span>
    <span class="brand-name">Ridgeline Pet Vision Care</span>
  </div>

  <div class="contact-block">
    <h1 class="person-name">
      <svg viewBox="0 0 20 22" aria-hidden="true"><path d="M0 0 L20 11 L0 22 Z"/></svg>
      Delia Vossman
    </h1>
    <p class="credentials">BSc, DVM, MSc, DipACVO</p>
    <p class="role">Veterinary Ophthalmologist</p>

    <p class="address">1874 Thornbury Rd<br>Kelowna, BC, V1X 4M9</p>

    <ul class="contact-list">
      <li>
        <svg viewBox="0 0 24 24" aria-hidden="true"><path fill="var(--teal)" d="M6.6 10.8a15.1 15.1 0 0 0 6.6 6.6l2.2-2.2a1 1 0 0 1 1-.25 11.4 11.4 0 0 0 3.6.57 1 1 0 0 1 1 1V20a1 1 0 0 1-1 1A17 17 0 0 1 3 4a1 1 0 0 1 1-1h3.5a1 1 0 0 1 1 1c0 1.25.2 2.45.57 3.57a1 1 0 0 1-.25 1z"/></svg>
        250.418.3927
      </li>
      <li>
        <svg viewBox="0 0 24 24" aria-hidden="true"><rect x="2" y="5" width="20" height="14" rx="1.5" fill="var(--teal)"/><path d="M2.5 6 L12 13 L21.5 6" fill="none" stroke="var(--card)" stroke-width="1.8"/></svg>
        ridgelinepetvisioncare@mailbox-example.net
      </li>
      <li>
        <svg viewBox="0 0 24 24" aria-hidden="true"><circle cx="12" cy="12" r="10" fill="var(--teal)"/><path d="M2 12h20M12 2c3 3 3 17 0 20M12 2c-3 3-3 17 0 20" fill="none" stroke="var(--card)" stroke-width="1.5"/></svg>
        ridgelinepetvisioncare-example.net
      </li>
    </ul>
  </div>
</section>

</body>
</html>
```